Business card design

We need a business card designed completed for a new company. We are a company that works with associations, schools to convert their older text/DVDs into dynamic online and mobile programs. Our initial platform is designed for the legal associations and will enable their lawyers to access their content such as forms, videos, case law and support materials anywhere, anytime. We are also focused on Project Management Associations, Financial Management Associations and IT Associations.

I would like for the business card to have the following information:

Logo

Kent marrowby

President and CEO

kmarrowby@trevantiq.example

Mobile: 555-374-9160

www.trevantiq.example

Tag line: Transforming content into a mobile platform    

I would like it to be double sided, use the colours of the logo, tie into the mobile world

 

Industry/Entity Type

Legal

Logo Text

Trevantiq

```html
<!DOCTYPE html>
<html lang="en">
<head>
<meta charset="utf-8">
<title>Trevantiq business card</title>
<link rel="stylesheet" href="https://fonts.googleapis.com/css2?family=Open+Sans:ital,wght@0,400;0,700;1,700&display=swap">
<style>
:root{
  --page:#ece9e4;
  --label:#2a2a2a;
  --band:#666666;
  --card-grey:#9b9b9b;
  --card-white:#ffffff;
  --stripe-white:#ffffff;
  --stripe-grey:#9b9b9b;
  --ink-light:#ffffff;
  --ink-dark:#1f1f1f;
  --ink-soft:#8a8a8a;
  --logo-dark:#5f5f5f;
}
*{margin:0;padding:0;box-sizing:border-box}
html,body{width:1200px;height:800px;overflow:hidden}
body{background:var(--page);font-family:"Open Sans",Arial,sans-serif;position:relative}
.side-label{position:absolute;width:510px;text-align:center;font-size:21px;color:var(--label);line-height:1}
.card{position:absolute;width:510px;height:290px;border-radius:22px;overflow:hidden;box-shadow:0 6px 14px rgba(0,0,0,.25)}
.card--grey{background:var(--card-grey)}
.card--white{background:var(--card-white)}
.card__wave{position:absolute;inset:0;width:510px;height:290px}
.wave-band{fill:var(--band)}
.stripe--white{fill:var(--stripe-white)}
.stripe--grey{fill:var(--stripe-grey)}
.holder{position:absolute;right:42px;top:28px;text-align:right;color:var(--ink-light)}
.holder__name{font-size:17px;line-height:22px}
.holder__title{font-size:13px;line-height:20px}
.logo-name{position:absolute;font-weight:700;letter-spacing:.5px;line-height:1}
.logo-name--small{left:20px;top:128px;font-size:46px}
.logo-name--large{left:0;right:0;top:112px;text-align:center;font-size:72px}
.on-grey{color:var(--ink-light)}
.on-white{color:var(--logo-dark)}
.tagline{position:absolute;left:27px;top:222px;font-size:15px;line-height:20px}
.tagline--light{color:var(--ink-light)}
.tagline--soft{color:var(--ink-soft)}
.contacts{position:absolute;right:42px;top:198px;list-style:none;text-align:right;font-size:13px;line-height:23px;color:var(--ink-dark)}
.contacts b{font-style:italic;font-weight:700}
.web-line{position:absolute;left:0;right:0;bottom:18px;text-align:center;font-size:15px;letter-spacing:3px;color:var(--ink-dark)}
</style>
</head>
<body>

<div class="side-label" style="left:80px;top:52px">Front</div>
<div class="side-label" style="left:625px;top:52px">Back - 1</div>
<div class="side-label" style="left:73px;top:412px">Back - 2</div>
<div class="side-label" style="left:633px;top:412px">Back - 3</div>

<section class="card card--grey" style="left:80px;top:97px">
  <svg class="card__wave" viewBox="0 0 510 290" aria-hidden="true">
    <path class="wave-band" d="M0 0H510V82C430 90 330 88 230 62C140 38 70 30 0 40Z"/>
    <path class="stripe--white" d="M0 40C70 30 140 38 230 62C330 88 430 90 510 82V92C430 100 330 98 230 74C140 52 70 58 0 72Z"/>
  </svg>
  <div class="holder">
    <div class="holder__name">Kent marrowby</div>
    <div class="holder__title">President and CEO</div>
  </div>
  <div class="logo-name logo-name--small on-grey">Trevantiq</div>
  <p class="tagline tagline--light">Transforming content<br>into a mobile platform</p>
  <ul class="contacts">
    <li><b>c</b> : 555-374-9160</li>
    <li><b>e</b> : kmarrowby@trevantiq.example</li>
    <li><b>w</b> : www.trevantiq.example</li>
  </ul>
</section>

<section class="card card--white" style="left:625px;top:97px">
  <svg class="card__wave" viewBox="0 0 510 290" aria-hidden="true">
    <path class="wave-band" d="M0 0H510V82C430 90 330 88 230 62C140 38 70 30 0 40Z"/>
    <path class="stripe--grey" d="M0 40C70 30 140 38 230 62C330 88 430 90 510 82V92C430 100 330 98 230 74C140 52 70 58 0 56Z"/>
  </svg>
  <div class="holder">
    <div class="holder__name">Kent marrowby</div>
    <div class="holder__title">President and CEO</div>
  </div>
  <div class="logo-name logo-name--small on-white">Trevantiq</div>
  <p class="tagline tagline--soft">Transforming content<br>into a mobile platform</p>
  <ul class="contacts">
    <li><b>c</b> : 555-374-9160</li>
    <li><b>e</b> : kmarrowby@trevantiq.example</li>
    <li><b>w</b> : www.trevantiq.example</li>
  </ul>
</section>

<section class="card card--grey" style="left:73px;top:452px">
  <div class="logo-name logo-name--large on-grey">Trevantiq</div>
  <div class="web-line">www.trevantiq.example</div>
</section>

<section class="card card--white" style="left:633px;top:450px">
  <div class="logo-name logo-name--large on-white">Trevantiq</div>
  <div class="web-line">www.trevantiq.example</div>
</section>

</body>
</html>
```